Book Cover: Quiet Harbor: Small Ceremonies For The Restless Soul

I would like a full cover spread- front, back and spine as well as a stand alone front cover for Kindle for the book. Design a cover that mirrors the profound depth and dynamic energy of 'Quiet Harbor.' Envision a visual tapestry that draws readers into a transformative journey, where spirituality and self-care unite. Explore vibrant colors, intricate textures, and a sense of inner radiance that beckons readers to explore the book's rich wisdom within. See images for design inspiration attached. Even though some of the images are cartoon, I'd like the cover to be more serious than playful and very elegant.

About this book (back cover copy)
Are you ready to embark on a transformative journey and elevate your daily existence? "Quiet Harbor" is a treasure trove of practical yet profound rituals and wisdom from renowned self-care, healing, and spirituality experts.

Within these pages, you'll uncover a tapestry of guidance and insight from some of the world's most respected mentors. Their collective wisdom is your key to creating a sacred sanctuary within your everyday life.

From invigorating morning rituals to meditative practices, empowering affirmations, and transformative energy healing, you'll find a rich tapestry of tools to nurture a deeper connection with yourself and the universe.

Whether you're a seasoned practitioner or a newcomer to the world of self-care and spirituality, "Quiet Harbor" is your trusted companion on the journey to transform your life and elevate your daily experience. Open this book today and start your sacred, fulfilling adventure.

Colors
0094D4
00A9DD
6FCCEA
C7EBF8
E9F6FB
E54698
E96AAD
F1A4CE
F9D9EA
FCEFF6
6B429C
8869AF
B7A5CE
E3DAEB
F3F0F8

Requirements
Must have
• Title: Quiet Harbor: Subtitle: Small Ceremonies For The Restless Soul Name of Publisher: Lantern Bough Publishing- Logo on the back Back cover copy

```html
<!DOCTYPE html>
<html lang="en">
<head>
<meta charset="utf-8">
<title>Quiet Harbor – Front Cover</title>
<link href="https://fonts.googleapis.com/css2?family=Playfair+Display:wght@400&family=Great+Vibes&family=Raleway:wght@800&display=swap" rel="stylesheet">
<style>
  :root {
    --stage: #d9d6d2;
    --title-ink: #3b3838;
    --script-ink: #ffffff;
    --caption-ink: #ffffff;
    --art-pink: #e54698;
    --art-rose: #f1a4ce;
    --art-orange: #f6a23a;
    --art-yellow: #f7d24a;
    --art-blue: #00a9dd;
    --art-sky: #6fccea;
    --art-purple: #6b429c;
    --art-night: #1f2350;
    --art-red: #d8264f;
  }
  * { margin: 0; padding: 0; box-sizing: border-box; }
  html, body {
    width: 1200px;
    height: 800px;
    overflow: hidden;
    background: var(--stage);
  }
  .stage {
    width: 1200px;
    height: 800px;
    display: flex;
    align-items: center;
    justify-content: center;
  }
  .front-cover {
    position: relative;
    width: 510px;
    height: 765px;
    overflow: hidden;
    box-shadow: 0 10px 30px rgba(0,0,0,0.25);
  }
  .cover-art {
    position: absolute;
    inset: 0;
    background:
      radial-gradient(ellipse 38% 26% at 50% 44%, var(--art-yellow) 0%, rgba(247,210,74,0.6) 45%, rgba(247,210,74,0) 100%),
      radial-gradient(ellipse 30% 40% at 18% 55%, var(--art-blue) 0%, rgba(0,169,221,0) 100%),
      radial-gradient(ellipse 30% 40% at 84% 58%, var(--art-sky) 0%, rgba(111,204,234,0) 100%),
      radial-gradient(ellipse 50% 30% at 50% 96%, var(--art-orange) 0%, rgba(246,162,58,0) 100%),
      linear-gradient(180deg,
        var(--art-rose) 0%,
        var(--art-orange) 14%,
        var(--art-pink) 26%,
        var(--art-purple) 48%,
        var(--art-night) 60%,
        var(--art-red) 76%,
        var(--art-pink) 100%);
  }
  .title {
    position: absolute;
    left: 20px;
    right: 20px;
    top: 18px;
    text-align: center;
    font-weight: 400;
  }
  .title-serif {
    display: block;
    font-family: "Playfair Display", serif;
    font-size: 132px;
    line-height: 1;
    letter-spacing: 2px;
    color: var(--title-ink);
  }
  .title-script {
    display: block;
    margin-top: -58px;
    padding-left: 60px;
    font-family: "Great Vibes", cursive;
    font-size: 118px;
    line-height: 1.1;
    color: var(--script-ink);
    white-space: nowrap;
  }
  .subtitle {
    position: absolute;
    left: 40px;
    right: 40px;
    top: 560px;
    text-align: center;
    font-family: "Raleway", sans-serif;
    font-weight: 800;
    font-size: 25px;
    line-height: 1.2;
    text-transform: uppercase;
    color: var(--caption-ink);
  }
  .author {
    position: absolute;
    left: 0;
    right: 0;
    bottom: 58px;
    text-align: center;
    font-family: "Playfair Display", serif;
    font-weight: 400;
    font-size: 30px;
    letter-spacing: 22px;
    padding-left: 22px;
    color: var(--caption-ink);
  }
</style>
</head>
<body>
  <main class="stage">
    <section class="front-cover">
      <div class="cover-art" role="img" aria-label="Vivid painted illustration of a serene figure with long flowing blue, purple and crimson hair, surrounded by radiant pink, orange and yellow blossoms"></div>
      <h1 class="title">
        <span class="title-serif">QUIET</span>
        <span class="title-script">Harbor</span>
      </h1>
      <p class="subtitle">Small Ceremonies For The<br>Restless Soul</p>
      <p class="author">AUTHOR NAME</p>
    </section>
  </main>
</body>
</html>
```